The Quiet Harvest Book Cover

Cover for Multiauthor Ebook & Paper Print Book Cover

Book Title:
The Quiet Harvest: Lessons of Insight From A Circle of Mentors to Guide You Toward a Fuller Journey

This book will offer the wisdom and philosophies of a variety of different coaches to allow future clients to get a taste of you and your style and prepare them to work with you!

A coach does not fix you. Or heal you. They coach you - offer thoughts to ponder, guidance, techniques to try. All to help you plays and succeed at the game of life.

Each coach has their own personality, training, experience, method and philosophy they bring to the table. The underlying purpose is to guide you through the quiet harvest, to become the person you desire and aspire to be. Different coaches for different folks, yet they all have their own unique wisdom and special sauce to share.

This book is a collection of just that. A tasting of the wisdom and philosophies of a variety of different coaches for you to experience.

Types of Coaches: Clarity, Dreams, Goals, Motivation, Mindset,  Subconscious, Beliefs, Behavior, Accountability, Life, Wellness, Love & Dating, Relationships, Sex, Business, Career,  Executive,  Personal Development,  Writing, Wellness, Fitness, Parenting,  Style, Spirituality, Public Speaking, Financial,  Time management, Weight Loss, Running, Self esteem,  Tarot, Astrology, Enneagram, Soul path/ Dharma, Skills, Performance,  Speaking / Communication, Leadership, Shadow Work, Acting, Sports, ANY & ALL

Target Market(s)

Males or females looking for guidance and words of wisdom from an expert coach - maybe to find one that resonates with them to work with further. Ages 16 and up. Any Gender. International. Looking to improve their life!

Industry/Entity Type

Self Development, Wellness, Coaching, Personal Growth, Fitness, Spirituality, Business, Relationships

Font styles to use
Serif
Script

Colors
0054AA
0677BA
7BADD7
CADEEF
E8F1F8
FFF300
FFF600
FEFA6F
FFFEC7
FFFEE8

Requirements
Must have
• I am looking for a visually appealing, unique cover that encompasses the breadth and depth of the transformation that people can go through and inspires them to want to grow and change even more. I love when elegant and classic simplicity is combined with some kind of twist that catches the eye and provokes thought. I love complimentary fonts, colors, design elements. You can visit my Brindlemart Author Page - Dr. Marisol Pendergast Voyle to see my titles to see what I have liked! But I am also excited to see where you can make my vision even better!!
Nice to have
• Front Cover - Image, Title and Subtitle, The Lantern Publishing House, Spine - Title and Publishing House Logo, Back - Book Blurb, Authors Names, Info about Publishing House, ISBN Barcode
Should not have
• Anything too feminine or too masculine as I want to encourage coaches of all genders to participate.

```html
<!DOCTYPE html>
<html lang="en">
<head>
<meta charset="utf-8">
<title>The Quiet Harvest — Book Cover</title>
<link rel="stylesheet" href="https://fonts.googleapis.com/css2?family=Kaushan+Script&family=Montserrat:wght@700&family=Playfair+Display:wght@500&display=swap">
<style>
  :root {
    --paper: #ececed;
    --paper-light: #f7f7f8;
    --ink: #262626;
    --title-warm: #ec5a2c;
    --title-hot: #d6185c;
    --publisher: #c8174e;
    --art-gold: #fcb731;
    --art-pale: #fdd89a;
    --art-orange: #f4742a;
    --art-red: #e2263e;
    --art-plum: #7c2d6a;
  }
  * { margin: 0; padding: 0; box-sizing: border-box; }
  html, body { width: 787px; height: 1200px; overflow: hidden; background: var(--paper); }
  .cover {
    position: relative;
    width: 787px;
    height: 1200px;
    overflow: hidden;
    background: radial-gradient(ellipse at 40% 30%, var(--paper-light), var(--paper) 70%);
  }

  .title { position: absolute; inset: 0; font-family: "Kaushan Script", cursive; font-weight: 400; }
  .title-the {
    position: absolute; left: 182px; top: 60px;
    font-size: 92px; line-height: 1; color: var(--ink);
  }
  .title-quiet {
    position: absolute; left: 30px; top: 140px;
    font-size: 136px; line-height: 1; letter-spacing: -1px; white-space: nowrap;
    background: linear-gradient(90deg, var(--title-warm), var(--title-hot) 80%);
    -webkit-background-clip: text; background-clip: text; color: transparent;
  }
  .title-swash { position: absolute; left: 104px; top: 246px; width: 172px; height: 36px; }
  .title-harvest {
    position: absolute; left: 338px; top: 242px;
    font-size: 100px; line-height: 1; color: var(--ink); white-space: nowrap;
  }

  .subtitle {
    position: absolute; left: 0; right: 0; top: 384px;
    font-family: "Montserrat", sans-serif; font-weight: 700;
    font-size: 27px; line-height: 36px; text-align: center;
    color: var(--ink); text-transform: uppercase;
  }

  .cover-art { position: absolute; inset: 0; pointer-events: none; }
  .art-flock {
    position: absolute; left: 0; top: 500px; width: 560px; height: 420px;
    border-radius: 0 240px 260px 0 / 0 200px 220px 0;
    background: linear-gradient(160deg, var(--art-gold) 0%, var(--art-red) 28%, var(--art-plum) 50%, var(--art-orange) 75%, var(--art-gold) 100%);
    opacity: 0.85;
    filter: blur(6px);
  }
  .art-figure {
    position: absolute; left: 300px; top: 600px; width: 415px; height: 600px;
    border-radius: 210px 190px 0 0;
    background: linear-gradient(180deg, var(--art-red) 0%, var(--art-orange) 30%, var(--art-gold) 60%, var(--art-pale) 100%);
    opacity: 0.92;
    filter: blur(4px);
  }

  .publisher {
    position: absolute; left: 40px; top: 1030px;
    font-family: "Playfair Display", serif; font-weight: 500;
    font-size: 38px; line-height: 45px; color: var(--publisher);
  }
</style>
</head>
<body>
<main class="cover">
  <h1 class="title">
    <span class="title-the">The</span>
    <span class="title-quiet">Quiet</span>
    <svg class="title-swash" viewBox="0 0 172 36" aria-hidden="true">
      <path d="M2 32 C50 14 110 4 170 6 L170 12 C112 12 58 22 6 36 Z" fill="var(--art-plum)" opacity="0.85"/>
    </svg>
    <span class="title-harvest">Harvest</span>
  </h1>

  <p class="subtitle">Lessons of insight from a<br>circle of mentors to guide<br>you toward a fuller journey</p>

  <div class="cover-art" role="img" aria-label="Illustration area: a figure seen in profile whose hair dissolves into a flock of warm-coloured butterflies">
    <div class="art-flock"></div>
    <div class="art-figure"></div>
  </div>

  <p class="publisher">The Lantern<br>Publishing<br>House</p>
</main>
</body>
</html>
```